Debt Collection Website Design! We are the solution for landlords to get paid what they are owed.

We are a 3rd party debt collection company that specializes in Residential and Commercial real estate debt collection. We help landlords recover money from past residents by being fair, friendly and aggressive. We also collect/buy/sell/trade civil judgments won resulting from anything from automobile accidents to evictions to a pet zebra getting stolen. We buy single judgments to large portfolios, we also collect judgments for a nominal fee.

I would like a new, modern, easy to navigate website. A spot that we can post news stories or updated information about our company. I have included our company logo that must be on the top of the page. Feel free to ask any questions that will help get the process going.

Target Market(s)

Landlords, small to large apartment complex. Real estate services and lawyers.

Industry/Entity Type

Real Estate

Number of Pages Required

3 page

Requirements
Must have
• Company logo which has been attached. A page where we can explain the collection process, fees and placement. A page where we can explain judgments, collection vs. selling, placement form. I am open to any font/designs and willing to work with anyone.
Nice to have
• Nice to have a spot on the homepage to place news articles about ourselves and our industry.
Should not have
• I don't want it over crowded. Simple, sleek and easy to navigate is best. No gavels on any of the pages. It cannot look legal, say/show anything that we use legal powers to collect. We are not a law office, we don't practice law, we are 3rd party debt collection agency.

```html
<!DOCTYPE html>
<html lang="en">
<head>
<meta charset="utf-8">
<title>Bellmere Partners</title>
<link href="https://fonts.googleapis.com/css2?family=Cinzel:wght@400;700&family=Open+Sans:wght@400;600;700&display=swap" rel="stylesheet">
<style>
:root{
  --navy:#1d4a7c;
  --navy-dark:#153860;
  --blue:#2a5d9f;
  --ink:#2b2b2b;
  --muted:#7a7a7a;
  --line:#dcdcdc;
  --white:#ffffff;
  --paper:#f4f4f4;
}
*{box-sizing:border-box;margin:0;padding:0}
html,body{width:1200px;height:2192px;overflow:hidden}
body{font-family:"Open Sans",Arial,sans-serif;color:var(--ink);background:var(--white);position:relative}

/* header */
.site-header{position:absolute;top:0;left:0;width:1200px;height:128px;background:var(--white);display:flex;align-items:center;justify-content:space-between;padding:0 110px}
.brand{display:flex;align-items:center;gap:10px}
.brand-dot{width:14px;height:14px;border-radius:50%;background:var(--ink)}
.brand-name{font-family:"Open Sans",Arial,sans-serif;font-weight:600;font-size:20px;color:var(--ink);letter-spacing:.3px}
.main-nav{display:flex;gap:10px;align-items:center}
.main-nav a{font-family:"Cinzel",Georgia,serif;font-size:13px;color:var(--ink);text-decoration:none;padding:10px 22px;letter-spacing:.5px}
.main-nav a.active{background:var(--navy);color:var(--white)}

/* hero */
.hero{position:absolute;top:128px;left:0;width:1200px;height:624px;overflow:hidden}
.hero-photo{position:absolute;inset:0;background:linear-gradient(135deg,#8a8d91 0%,#5c6066 40%,#3e4248 70%,#6d7075 100%)}
.hero-shade{position:absolute;inset:0;background:rgba(20,24,30,.35)}
.hero-copy{position:absolute;top:250px;left:0;width:1200px;text-align:center;color:var(--white)}
.hero-copy h1{font-family:"Cinzel",Georgia,serif;font-size:28px;font-weight:700;letter-spacing:.5px}
.hero-copy p{font-size:14px;line-height:22px;margin:22px auto 0;width:620px}
.btn{display:inline-block;background:var(--navy);color:var(--white);font-family:"Cinzel",Georgia,serif;font-size:12px;letter-spacing:.5px;padding:11px 26px;text-decoration:none}
.hero-copy .btn{margin-top:24px}
.hero-arrow{position:absolute;top:262px;width:30px;height:44px;background:rgba(0,0,0,.35);display:flex;align-items:center;justify-content:center}
.hero-arrow.prev{left:30px}
.hero-arrow.next{right:30px}
.scroll-cue{position:absolute;left:585px;top:540px}

/* section titles */
.section-title{font-family:"Cinzel",Georgia,serif;font-size:34px;text-align:center;color:var(--ink);letter-spacing:.5px}
.title-rule{width:70px;height:2px;background:var(--navy);margin:14px auto 0}

/* welcome */
.welcome{position:absolute;top:752px;left:0;width:1200px;height:330px;text-align:center;padding-top:40px}
.welcome p{width:880px;margin:30px auto 0;font-size:12px;line-height:20px;color:var(--muted)}
.welcome .btn{margin-top:34px}

/* services */
.services{position:absolute;top:1082px;left:0;width:1200px;height:520px}
.cards{position:absolute;top:80px;left:100px;width:1000px;display:flex;gap:32px}
.card{width:312px;height:380px;background:var(--white);box-shadow:0 2px 8px rgba(0,0,0,.18);text-align:center}
.card-photo{height:200px}
.card-photo.residential{background:linear-gradient(180deg,#cfd9e4 0%,#e9edf1 55%,#b9c2ca 100%)}
.card-photo.commercial{background:linear-gradient(180deg,#3f6fa8 0%,#7ea2c9 50%,#2d5584 100%)}
.card-photo.debt{background:linear-gradient(135deg,#e8e2d8 0%,#b9b1a4 50%,#d9d3c9 100%)}
.card h3{font-family:"Cinzel",Georgia,serif;font-size:16px;margin-top:18px;letter-spacing:.5px}
.card h4{font-size:11px;font-weight:700;margin-top:8px}
.card p{font-size:11px;line-height:17px;color:var(--muted);width:250px;margin:8px auto 0}
.card .btn{margin-top:14px;padding:8px 20px;font-size:11px}

/* news */
.news{position:absolute;top:1602px;left:0;width:1200px;height:338px}
.news .section-title{padding-top:28px}
.news-list{position:absolute;top:118px;left:100px;width:1000px;display:flex;gap:40px}
.news-item{width:480px;display:flex;gap:18px;padding-bottom:22px;border-bottom:1px solid var(--line);box-shadow:0 14px 14px -14px rgba(0,0,0,.35)}
.news-photo{width:160px;height:122px;flex:none}
.news-photo.one{background:linear-gradient(135deg,#d6d9dc 0%,#9ea4aa 100%)}
.news-photo.two{background:linear-gradient(135deg,#cbd3db 0%,#7f8a95 100%)}
.news-item h3{font-family:"Cinzel",Georgia,serif;font-size:16px;letter-spacing:.5px}
.news-date{font-size:10px;color:var(--muted);margin-top:6px}
.news-item p{font-size:11px;line-height:17px;color:var(--muted);margin-top:8px}

/* footer */
.site-footer{position:absolute;top:1940px;left:0;width:1200px;height:188px;background:var(--navy);color:var(--white);display:flex;padding:22px 80px 0;gap:40px}
.footer-col{width:230px}
.footer-col h4{font-family:"Cinzel",Georgia,serif;font-size:20px;font-weight:400;margin-bottom:10px}
.footer-col p,.footer-col li{font-size:10px;line-height:16px;color:#d5deea}
.footer-col ul{list-style:none}
.post{display:flex;gap:8px;margin-bottom:10px}
.post-thumb{width:26px;height:26px;background:#5b7ea8;flex:none}
.post small{display:block;font-size:9px;color:#a9bbd2}
.contact-line{display:flex;align-items:center;gap:8px;margin-bottom:8px}
.news-field{width:200px;height:22px;background:var(--white);margin-top:6px;font-size:9px;color:var(--muted);padding:4px 8px}
.news-submit{display:inline-block;margin-top:6px;background:var(--blue);font-size:10px;line-height:14px;padding:4px 14px;border:1px solid #5b7ea8}
.footer-bottom{position:absolute;top:2128px;left:0;width:1200px;height:64px;background:var(--navy-dark);color:#c7d3e2;font-size:10px;padding:12px 80px 0;display:flex;justify-content:space-between}
.socials{display:flex;gap:6px;margin-top:8px}
.socials span{width:16px;height:16px;border:1px solid #c7d3e2;border-radius:50%}
</style>
</head>
<body>

<header class="site-header">
  <div class="brand">
    <div class="brand-dot"></div>
    <div class="brand-name">Bellmere Partners</div>
  </div>
  <nav class="main-nav">
    <a class="active" href="#">Home</a>
    <a href="#">Services</a>
    <a href="#">Blog</a>
    <a href="#">Features</a>
    <a href="#">About us</a>
    <a href="#">Contact us</a>
  </nav>
</header>

<section class="hero">
  <div class="hero-photo" role="img" aria-label="Photo of a team reviewing paperwork and charts at a desk"></div>
  <div class="hero-shade"></div>
  <div class="hero-arrow prev"><svg width="10" height="16"><path d="M8 2 L2 8 L8 14" stroke="#fff" stroke-width="2" fill="none"/></svg></div>
  <div class="hero-arrow next"><svg width="10" height="16"><path d="M2 2 L8 8 L2 14" stroke="#fff" stroke-width="2" fill="none"/></svg></div>
  <div class="hero-copy">
    <h1>We Help Landlords Recover Money From Past Residents</h1>
    <p>Keep a healthy cash flow with a partner that is fair, friendly and firm, a long established team that brings your unpaid balances back home.</p>
    <a class="btn" href="#">View More Info</a>
  </div>
  <svg class="scroll-cue" width="30" height="48" viewBox="0 0 30 48"><rect x="2" y="2" width="26" height="44" rx="13" fill="none" stroke="#fff" stroke-width="2"/><line x1="15" y1="11" x2="15" y2="19" stroke="#fff" stroke-width="2"/></svg>
</section>

<section class="welcome">
  <h2 class="section-title">Welcome to Bellmere Partners</h2>
  <div class="title-rule"></div>
  <p>We are a third party collection agency that focuses on residential and commercial real estate balances. Our team works with landlords, apartment communities and property managers to recover money owed by past residents. We treat every account with fairness and respect while staying persistent until the balance is resolved. We also buy, sell and collect civil judgments of every size, from single accounts to large portfolios, for a modest fee that keeps more money in your pocket.</p>
  <a class="btn" href="#">Read More</a>
</section>

<section class="services">
  <h2 class="section-title">Our Services</h2>
  <div class="title-rule"></div>
  <div class="cards">
    <article class="card">
      <div class="card-photo residential" role="img" aria-label="Photo of a modern residential building"></div>
      <h3>Residential</h3>
      <h4>We help landlords recover money</h4>
      <p>Recovering balances left by past residents of apartments, homes and managed rental properties.</p>
      <a class="btn" href="#">View More</a>
    </article>
    <article class="card">
      <div class="card-photo commercial" role="img" aria-label="Photo of glass office towers against a blue sky"></div>
      <h3>Commercial</h3>
      <h4>We help landlords recover money</h4>
      <p>Collecting unpaid rent and fees from former tenants of offices, shops and commercial spaces.</p>
      <a class="btn" href="#">View More</a>
    </article>
    <article class="card">
      <div class="card-photo debt" role="img" aria-label="Photo of colleagues discussing documents at a table"></div>
      <h3>Debt Collection</h3>
      <h4>We help landlords recover money</h4>
      <p>Buying, selling and collecting civil judgments, from single accounts to large portfolios.</p>
      <a class="btn" href="#">View More</a>
    </article>
  </div>
</section>

<section class="news">
  <h2 class="section-title">Latest News</h2>
  <div class="title-rule"></div>
  <div class="news-list">
    <article class="news-item">
      <div class="news-photo one" role="img" aria-label="Photo of a meeting with laptops"></div>
      <div>
        <h3>Sed Do Eiusmod Tempor</h3>
        <div class="news-date">OCT 10, 2014</div>
        <p>Our team shares new tips for landlords on tracking past due balances, keeping clear records and placing accounts early for the best results.</p>
      </div>
    </article>
    <article class="news-item">
      <div class="news-photo two" role="img" aria-label="Photo of hands reviewing printed reports"></div>
      <div>
        <h3>Labore et Dolore Beatae</h3>
        <div class="news-date">OCT 10, 2014</div>
        <p>Industry update on judgment portfolios, recent market trends and what property managers should know before selling older accounts this year.</p>
      </div>
    </article>
  </div>
</section>

<footer class="site-footer">
  <div class="footer-col">
    <h4>About</h4>
    <p>Bellmere Partners is a third party collection agency serving landlords, apartment communities and real estate professionals with fair, friendly and persistent recovery of past due balances.</p>
  </div>
  <div class="footer-col">
    <h4>Latest Posts</h4>
    <div class="post"><div class="post-thumb"></div><p>How to Place Older Accounts Early<small>March 15, 2014</small></p></div>
    <div class="post"><div class="post-thumb"></div><p>How to Place Older Accounts Early<small>March 15, 2014</small></p></div>
  </div>
  <div class="footer-col">
    <h4>Contact Info</h4>
    <div class="contact-line"><svg width="10" height="12"><path d="M5 11 C1 6 1 4 1 4 A4 4 0 0 1 9 4 C9 4 9 6 5 11Z" fill="#fff"/></svg><p>Address: 48 Alder Street, Fairview</p></div>
    <div class="contact-line"><svg width="10" height="12"><path d="M2 1 L4 1 L5 4 L3.5 5 Q4.5 7.5 6.5 8.5 L7.5 7 L10 8 L10 10 Q4 11 1 3Z" fill="#fff"/></svg><p>Phone: (555) 014-2280</p></div>
    <div class="contact-line"><svg width="10" height="12"><rect x="1" y="3" width="8" height="7" fill="#fff"/></svg><p>Fax: (555) 014-2281</p></div>
    <div class="contact-line"><svg width="10" height="12"><rect x="0.5" y="3" width="9" height="6" fill="none" stroke="#fff"/><path d="M0.5 3 L5 7 L9.5 3" stroke="#fff" fill="none"/></svg><p>info@bellmere-example.com</p></div>
  </div>
  <div class="footer-col">
    <h4>Newsletter</h4>
    <p>Sign up for our newsletter and get the latest news.</p>
    <div class="news-field">Your name</div>
    <div class="news-field">Your email</div>
    <span class="news-submit">Submit</span>
  </div>
</footer>

<div class="footer-bottom">
  <div>
    <div>Privacy Policy &nbsp;|&nbsp; Store Locator &nbsp;|&nbsp; Advanced Search &nbsp;|&nbsp; Terms &amp; Conditions</div>
    <div class="socials"><span></span><span></span><span></span><span></span><span></span></div>
  </div>
  <div>Copyright &copy; Bellmere Partners 2014. All Rights Reserved.</div>
</div>

</body>
</html>
```